Copper lark buildworks

Copper lark buildworks is a small construction company.
Who is a licenced builder, Carpenter, joiner,
working on heritage ,new build, speacial projects and sometimes furniture

Industry/Entity Type

Construction

```html
<!DOCTYPE html>
<html lang="en">
<head>
<meta charset="utf-8">
<title>Copper lark buildworks – Business Card</title>
<link rel="stylesheet" href="https://fonts.googleapis.com/css2?family=Marcellus&family=Lato:wght@400&display=swap">
<style>
  :root {
    --page-bg: #ecebe8;
    --card-green: #27ab17;
    --card-green-deep: #1e9810;
    --ring-green: #2aa81a;
    --disc-white: #f7f6f4;
    --logo-ink: #3d3b3c;
    --text-white: #ffffff;
  }
  * { box-sizing: border-box; margin: 0; padding: 0; }
  html, body {
    width: 1200px; height: 900px; overflow: hidden;
    background: var(--page-bg);
  }
  .card {
    position: absolute;
    left: 150px; top: 172px;
    width: 900px; height: 556px;
    background: linear-gradient(180deg, var(--card-green) 0%, var(--card-green-deep) 100%);
    border-radius: 278px 0 0 278px;
    box-shadow: 0 18px 40px rgba(0,0,0,0.18);
  }
  .brand-disc {
    position: absolute;
    left: 0; top: 0;
    width: 556px; height: 556px;
    border-radius: 50%;
    background: var(--disc-white);
    border: 7px solid var(--ring-green);
    display: flex; flex-direction: column;
    align-items: center; justify-content: center;
    gap: 22px;
  }
  .brand-dot {
    width: 64px; height: 64px; border-radius: 50%;
    background: var(--ring-green);
  }
  .brand-name {
    font-family: "Marcellus", serif;
    font-size: 40px;
    color: var(--logo-ink);
    letter-spacing: 0.5px;
  }
  .details {
    position: absolute;
    right: 44px; top: 0;
    text-align: right;
    color: var(--text-white);
    font-family: "Lato", sans-serif;
  }
  .person-name {
    position: absolute; right: 0; top: 62px;
    white-space: nowrap;
    font-family: "Marcellus", serif;
    font-size: 38px; font-weight: 400;
  }
  .person-role {
    position: absolute; right: 0; top: 110px;
    white-space: nowrap;
    font-size: 24px;
  }
  .contact-list {
    position: absolute; right: 0; top: 275px;
    list-style: none;
    font-size: 23px; line-height: 33px;
    white-space: nowrap;
  }
  .contact-list li { display: flex; align-items: center; justify-content: flex-end; gap: 8px; }
  .contact-list svg { width: 20px; height: 20px; fill: var(--text-white); }
  .address {
    position: absolute; right: 0; top: 425px;
    font-size: 23px; line-height: 31px;
    white-space: nowrap; font-style: normal;
  }
</style>
</head>
<body>
  <section class="card">
    <div class="brand-disc">
      <span class="brand-dot"></span>
      <span class="brand-name">Copper lark buildworks</span>
    </div>

    <div class="details">
      <h1 class="person-name">Harriet Vale</h1>
      <p class="person-role">Managing Director</p>

      <ul class="contact-list">
        <li>061-482 730 915
          <svg viewBox="0 0 20 20" aria-hidden="true"><path d="M2 7c0-3 3-4 8-4s8 1 8 4v2h-4V7H6v2H2z"/><path d="M5 10h10l2 7H3z"/></svg>
        </li>
        <li>071-395 264 108
          <svg viewBox="0 0 20 20" aria-hidden="true"><path d="M6 1h8a1 1 0 0 1 1 1v16a1 1 0 0 1-1 1H6a1 1 0 0 1-1-1V2a1 1 0 0 1 1-1zm1 2v12h6V3zm3 13a1 1 0 1 0 0 2 1 1 0 0 0 0-2z"/></svg>
        </li>
        <li>hello@copperlark.com
          <svg viewBox="0 0 20 20" aria-hidden="true"><path d="M1 4h18v12H1zm2 2v.5l7 5 7-5V6l-7 5z"/></svg>
        </li>
        <li>www.copperlarkbuild.com
          <svg viewBox="0 0 20 20" aria-hidden="true"><circle cx="10" cy="10" r="9"/><path d="M1.5 10h17M10 1.5c-3 3-3 14 0 17M10 1.5c3 3 3 14 0 17" stroke="#27ab17" stroke-width="1.4" fill="none"/></svg>
        </li>
      </ul>

      <address class="address">27 Tanner Row, Millbrook<br>Eastvale, 40218</address>
    </div>
  </section>
</body>
</html>
```